Women's Jewellery startup needs a captivating, beautifully designed and intuitive online store

[12/24 update]

Added 2 additional documents:

Feedback on designs received so far: designer feedback.docx
Product images from catalogue: products images.docx

Please read the feedback provided on designs provided so far to guide you further on your submission. The product images can be used to create promotional banners for the site.

@@@Added a document (VELISTO JEWELLERY_checklist.docx) which can be used by designers as a checklist when submitting their designs to ensure all aspects of the requirements have been covered @@@

+++IMPORTANT BUT NOT SPECIFIED IN THE REQUIREMENTS DOCUMENT - DESIGN SHOULD INCLUDE SUPPORT FOR MOBILE FRIENDLY SITE TOO+++

***Previous experience designing Jewellery online stores preferred (not essential)***

The name of the online Jewellery store is "Velisto Jewellery" and the business is based in Hong Kong. It will be run by 2 stay at home mothers. We need a Shopify themed store designed that will achieve the following objectives in order of priority:

• Conversion: The primary objective of the design/content is to prompt the customer to make a purchase. While this may sound obvious, it is mentioned so as not to distract the design process by focusing on other objectives (which are also important). The site also needs to be optimized so as to rank high in search engine searches for relevant keywords (SEO)
• Navigation: An intuitive interface which takes away a lot of the thinking from the customer by making it obvious what they need to do when they visit the store
• Engagement: Encourages the customer to spend time on the website and share content with their social network

Where applicable, the design of the store should reflect as closely as possible the mission statements and words outlined below:

• Jewellery you’ll fall in love with
• We want every client to leave the store with a smile
• We want to be able to provide the best service we can in every situation no matter what
• We aim to increase our business by word of mouth; therefore we tell people things about our store that makes it interesting for them to share
• We love every customer, no matter how difficult things get
• We, as a team, are so well informed about our products and brands that we always have the best information for our customers
• We celebrate women here!
• We celebrate life in here!
• We celebrate beauty here!
• We celebrate families here, as jewellery often stays within families.
• We will always try to make an extra step
• We will always try to exceed the expectation of our customers
• We will go as far as we possibly can to attract a customer back to our store and connect with us
• Every client that leaves our store knows more about jewellery because we passionately told him about it
• Romantic, classic, love, warm, cool, stylish

A draft functional specification is attached with this brief. We would like the design to reflect as closely as possible the functional requirements outlined in the document. Open to suggestions to improve upon the functional requirements.

Target Market(s)

Women aged 18-55

Industry/Entity Type

Jewelry Store

Coding

Coded - Design and coding required

Number of Pages Required

5+ page

Font styles to use
Other font styles liked:
• Myriad Pro as per Logo but open to any font that complements this one

Requirements
Must have
• 1. A look that encourages the user to make a purchase
• 2. An intuitive, easy to navigate and engaging interface
• 3. Primary colour scheme as defined in the functional specification attached
• 4. Simplistic look, not too cluttered
Nice to have
• 1. Closely matching the functional requirements of the site as outlined in the requirements specification but open to any better ideas

```html
<!DOCTYPE html>
<html lang="en">
<head>
<meta charset="utf-8">
<title>Velisto Jewellery</title>
<link rel="stylesheet" href="https://fonts.googleapis.com/css2?family=Montserrat:wght@400;500;600;700&family=Open+Sans:wght@400;600;700&display=swap">
<style>
:root{
  --dark:#1e1e1e;
  --footer:#262626;
  --ink:#222;
  --muted:#8a8a8a;
  --line:#e3e3e3;
  --soft:#f3f3f3;
  --gold:#c9a26b;
  --star:#e0b55a;
  --red:#c0392b;
  --white:#fff;
}
*{box-sizing:border-box;margin:0;padding:0}
html,body{width:1200px;height:5216px;overflow:hidden}
body{font-family:"Open Sans",sans-serif;color:var(--ink);background:var(--white);position:relative}
.abs{position:absolute}
h1,h2,h3,h4{font-family:"Montserrat",sans-serif}
.section{position:relative;width:1200px;overflow:hidden}
.btn{display:inline-block;border:1px solid #bbb;background:var(--white);font:600 11px "Montserrat",sans-serif;letter-spacing:1px;padding:12px 22px;color:var(--ink)}
.btn.dark{background:transparent;border-color:#fff;color:#fff}
.section-title{text-align:center;font-size:26px;font-weight:600;letter-spacing:1px}
.section-title::after{content:"";display:block;width:50px;height:2px;background:var(--gold);margin:14px auto 0}
.stars{color:var(--star);font-size:13px;letter-spacing:2px}

/* header */
.topbar{height:52px;background:var(--dark);color:#fff}
.menu-btn{left:0;top:0;width:52px;height:52px;background:#111;display:flex;align-items:center;justify-content:center}
.brand{left:100px;top:8px;color:#fff;text-align:center}
.brand .mark{display:inline-block;width:34px;height:34px;background:var(--gold);vertical-align:middle}
.brand .name{display:inline-block;vertical-align:middle;margin-left:10px;font:600 16px "Montserrat",sans-serif;letter-spacing:3px;color:#fff}
.nav{left:340px;top:0;height:52px;display:flex;gap:28px;align-items:center;font:600 11px "Montserrat",sans-serif;letter-spacing:1px;white-space:nowrap}
.nav-icons{left:800px;top:17px;display:flex;gap:30px}
.cart{left:960px;top:13px;display:flex;align-items:center;gap:10px;font-size:12px;white-space:nowrap}

/* hero */
.hero{height:488px;background:linear-gradient(90deg,#efefef 0%,#e8e8e8 60%,#dcdcdc 100%)}
.hero h1{left:100px;top:140px;font-size:42px;line-height:52px;font-weight:700;color:#1b1b1b}
.hero .offer{left:100px;top:258px;font:500 22px "Montserrat",sans-serif;letter-spacing:2px;color:#444}
.hero .btn{left:100px;top:330px}
.hero-photo{left:640px;top:0;width:400px;height:488px;background:radial-gradient(ellipse at 50% 40%,#d9c3b2 0%,#bfa897 35%,#9a8677 60%,rgba(230,230,230,0) 80%)}
.arrow{top:230px}

/* promos */
.promos{height:320px}
.promo{top:40px;width:312px;height:220px;color:#fff;font:600 15px/24px "Montserrat",sans-serif}
.promo p{position:absolute;left:22px;bottom:40px;width:220px}

/* products */
.products{height:700px}
.products .section-title{position:absolute;top:100px;width:100%}
.select{top:208px;height:34px;border:1px solid var(--line);font-size:11px;color:var(--muted);padding:9px 12px;display:flex;justify-content:space-between}
.filter{left:100px;top:280px;width:228px;height:200px;background:var(--soft)}
.filter .head{background:#3a3a3a;color:#fff;font:600 12px "Montserrat",sans-serif;padding:12px 14px;letter-spacing:1px}
.filter ul{list-style:none;padding:10px 14px;font-size:10px;color:#666}
.filter li{display:flex;justify-content:space-between;padding:6px 0;border-bottom:1px solid #e6e6e6}
.filter li.on{color:var(--gold)}
.range{height:3px;background:#ccc;margin:6px 14px;position:relative}
.range span{position:absolute;left:0;width:55%;height:3px;background:#4a6fa5}
.card{top:280px;width:232px;text-align:center}
.card .pic{height:200px;border:1px solid var(--line);background:#fff;display:flex;align-items:center;justify-content:center}
.card .pic i{display:block;width:110px;height:80px;border-radius:50%}
.card .tools{height:30px;background:var(--soft);display:flex;justify-content:center;gap:24px;align-items:center;font-size:11px;color:#555}
.card h4{font-size:12px;font-weight:500;letter-spacing:1px;margin-top:24px}
.card .price{font-size:12px;color:var(--muted);margin-top:14px}
.card .price .now{color:var(--red)}
.card .price s{margin-left:8px}

/* feature */
.feature{height:420px;background:var(--soft)}
.feature h2{left:100px;top:92px;font-size:32px;line-height:42px;font-weight:700}
.feature .lead{left:100px;top:196px;width:560px;font-size:11px;color:var(--muted)}
.feature .price{left:100px;top:236px;font:700 24px "Montserrat",sans-serif;color:var(--red)}
.feature .btn{left:100px;top:300px}
.feature-photo{left:740px;top:20px;width:240px;height:380px;background:radial-gradient(ellipse at 50% 55%,#d8d8d8 0%,#bdbdbd 35%,rgba(243,243,243,0) 70%)}

/* best sellers */
.best{height:808px}
.best .section-title{position:absolute;top:120px;width:100%}
.best .card{top:220px}
.best .card .pic{height:330px}
.best .card .pic i{width:120px;height:160px}

/* strip */
.strip{height:272px;display:flex}
.tile{flex:1;position:relative;color:#fff}
.tile .txt{position:absolute;top:50px}
.tile h3{font-size:26px;line-height:30px;font-weight:700}
.tile .sub{font-size:13px;color:var(--gold);margin-top:4px}
.tile .btn{margin-top:16px;padding:8px 16px;font-size:9px}

/* testimonials */
.testimonials{height:680px}
.t-box{left:100px;top:80px;width:1000px;height:520px;border:1px solid var(--line)}
.quote{left:120px;top:96px;font:700 120px/1 "Montserrat",sans-serif;color:#d8d8d8}
.testimonials .section-title{position:absolute;top:180px;width:100%}
.t-col{top:270px;width:420px;font-size:12px;line-height:22px;color:#777}
.person{display:flex;align-items:center;gap:16px;margin-top:28px}
.avatar{width:62px;height:62px;border-radius:50%;background:linear-gradient(135deg,#6b4f3e,#2e2520)}
.person b{display:block;font:600 11px "Montserrat",sans-serif;color:var(--gold);letter-spacing:1px}
.person small{font-size:10px;color:var(--muted)}
.dots{left:570px;top:540px;display:flex;gap:10px}
.dots i{width:8px;height:8px;border-radius:50%;background:#ccc}
.dots i:first-child{background:#555}

/* blog */
.blog{height:800px;background:var(--soft)}
.blog .section-title{position:absolute;top:120px;width:100%}
.post-img{position:absolute}
.post-txt{position:absolute;background:#fff;padding:26px 22px}
.post-txt h4{font-size:12px;line-height:18px;font-weight:600;letter-spacing:.5px}
.post-txt p{font-size:11px;line-height:19px;color:#888;margin-top:12px}
.post-txt a{display:block;font-size:11px;color:var(--gold);margin-top:12px;text-decoration:none}
.date{position:absolute;width:56px;height:56px;background:var(--gold);color:#fff;font:700 12px/16px "Montserrat",sans-serif;text-align:center;padding-top:12px}

/* perks */
.perks{height:140px;border-top:1px solid var(--line)}
.perk{top:46px;display:flex;gap:14px;align-items:center}
.perk b{display:block;font:600 12px "Montserrat",sans-serif;letter-spacing:.5px}
.perk small{font-size:10px;color:var(--muted)}
.pay{top:58px;display:flex;gap:8px}
.pay i{width:38px;height:24px;border:1px solid #ccc;background:#f6f6f6}

/* footer */
.footer{height:504px;background:var(--footer);color:#bbb}
.contacts{left:0;top:0;width:508px;height:504px;background:#1b1b1b;padding:60px 0 0 100px}
.footer h4{font-size:13px;letter-spacing:1px;color:#fff;font-weight:600}
.contacts ul{list-style:none;margin-top:26px;font-size:12px;line-height:20px}
.contacts li{display:flex;gap:14px;margin-bottom:18px}
.social{display:flex;gap:10px;margin-top:10px}
.social i{width:30px;height:30px;border-radius:50%;border:1px solid #777}
.fcol ul{list-style:none;margin-top:22px;font-size:12px}
.fcol li{margin-bottom:14px}
.fcol li::before{content:"›";margin-right:8px;color:#888}
.news{left:608px;top:340px}
.news .field{margin-top:22px;display:flex}
.news .field span{width:380px;height:40px;background:#fff}
.news .field b{width:112px;height:40px;background:var(--gold);color:#fff;font:600 11px "Montserrat",sans-serif;display:flex;align-items:center;justify-content:center;letter-spacing:1px}
.bottom{height:32px;background:#111;color:#777;font-size:10px;text-align:center;line-height:32px}
</style>
</head>
<body>

<header class="section topbar">
  <div class="abs menu-btn"><svg width="20" height="16"><path d="M0 2h20M0 8h20M0 14h20" stroke="#fff" stroke-width="2"/></svg></div>
  <div class="abs brand"><span class="mark"></span><span class="name">VELISTO</span></div>
  <nav class="abs nav"><span>HOME ▾</span><span>MY ACCOUNT</span><span>WISHLIST</span><span>JEWELS ▾</span><span>ABC ▾</span></nav>
  <div class="abs nav-icons">
    <svg width="18" height="18"><circle cx="9" cy="9" r="7" fill="none" stroke="#fff" stroke-width="2"/><circle cx="9" cy="9" r="2" fill="#fff"/></svg>
    <svg width="18" height="18"><circle cx="9" cy="6" r="4" fill="#fff"/><path d="M1 18c0-5 4-7 8-7s8 2 8 7z" fill="#fff"/></svg>
    <svg width="18" height="18"><circle cx="7" cy="7" r="5.5" fill="none" stroke="#fff" stroke-width="2"/><path d="M11 11l6 6" stroke="#fff" stroke-width="2"/></svg>
  </div>
  <div class="abs cart"><svg width="26" height="26"><path d="M2 4h4l3 13h12l3-9H8" fill="none" stroke="#fff" stroke-width="2"/><circle cx="10" cy="22" r="2" fill="#fff"/><circle cx="19" cy="22" r="2" fill="#fff"/></svg><span>0 items ($0.00)</span></div>
</header>

<section class="section hero">
  <svg class="abs arrow" style="left:40px" width="14" height="24"><path d="M12 2L2 12l10 10" fill="none" stroke="#333" stroke-width="2"/></svg>
  <h1 class="abs">WE CELEBRATE<br>WOMEN HERE!</h1>
  <p class="abs offer">UPTO 90 % OFFER</p>
  <span class="abs btn">SHOP NOW</span>
  <div class="abs hero-photo" role="img" aria-label="Model wearing a diamond necklace and earrings"></div>
  <svg class="abs arrow" style="left:1146px" width="14" height="24"><path d="M2 2l10 10L2 22" fill="none" stroke="#333" stroke-width="2"/></svg>
</section>

<section class="section promos">
  <div class="abs promo" style="left:100px;background:linear-gradient(135deg,#d8b57a,#a8844e)" role="img" aria-label="Gold diamond rings on fabric"><p>Extra 10% off Diamond rings till March 31st, 2018</p></div>
  <div class="abs promo" style="left:444px;background:radial-gradient(circle at 60% 40%,#7a2a4a,#2a0f1c 70%)" role="img" aria-label="Ruby rings on dark background"><p>Extra 10% off Ruby rings till March 31st, 2018</p></div>
  <div class="abs promo" style="left:788px;background:linear-gradient(135deg,#6f7780,#2a2f35)" role="img" aria-label="Emerald ring being crafted"><p style="top:40px;bottom:auto">Extra 10% off Emerald rings till March 31st, 2018</p></div>
</section>

<section class="section products">
  <h2 class="section-title">OUR PRODUCTS</h2>
  <div class="abs select" style="left:100px;width:228px"><span>Our Favourites</span><span>▾</span></div>
  <div class="abs select" style="left:352px;width:228px"><span>What's New</span><span>▾</span></div>
  <div class="abs select" style="left:604px;width:496px"><span>Price</span><span>▾</span></div>
  <aside class="abs filter">
    <div class="head">FILTER BY</div>
    <ul><li><span>TYPE</span><span>▾</span></li><li><span>COLLECTION</span><span>▾</span></li><li><span>METAL</span><span>▾</span></li><li><span>GEMSTONE</span><span>▾</span></li><li class="on"><span>PRICE RANGE</span><span>▾</span></li></ul>
    <div class="range"><span></span></div>
  </aside>
  <div class="abs card" style="left:352px"><div class="pic"><i role="img" aria-label="Diamond solitaire ring" style="background:radial-gradient(#d5d5d5,#fff 70%)"></i></div><div class="tools">♥ ⇄ ⊕</div><h4>RINGS</h4><p class="price">$78.00</p><div class="stars">★★★★★</div></div>
  <div class="abs card" style="left:608px"><div class="pic"><i role="img" aria-label="Gold bangles" style="background:radial-gradient(#e2b64e,#fff 70%)"></i></div><div class="tools">♥ ⇄ ⊕</div><h4>BRACELETS</h4><p class="price">$78.00</p><div class="stars">★★★★★</div></div>
  <div class="abs card" style="left:864px;width:236px"><div class="pic"><i role="img" aria-label="Ruby necklace" style="background:radial-gradient(#d84a5f,#fff 70%)"></i></div><div class="tools">♥ ⇄ ⊕</div><h4>NECKLACES</h4><p class="price">$78.00</p><div class="stars">★★★★★</div></div>
</section>

<section class="section feature">
  <h2 class="abs">VELISTO JEWELLERY<br>ONLINE STORE</h2>
  <p class="abs lead">Cras sed odio at accumsan lorem ut nibh dignissim mauris ut blandit pretium.</p>
  <p class="abs price">$ 68.00</p>
  <span class="abs btn">SHOP NOW</span>
  <div class="abs feature-photo" role="img" aria-label="Diamond necklace with gold pendant"></div>
</section>

<section class="section best">
  <h2 class="section-title">BEST SELLERS</h2>
  <div class="abs card" style="left:100px"><div class="pic"><i role="img" aria-label="Red gemstone pendant" style="background:radial-gradient(#c62a2a,#fff 65%)"></i></div><div class="tools">♥ ⇄ ⊕</div><h4>CHARMS</h4><p class="price"><span class="now">$198.00</span></p><div class="stars">★★★★★</div></div>
  <div class="abs card" style="left:356px"><div class="pic"><i role="img" aria-label="Pearl drop earrings" style="background:radial-gradient(#e9cdb0,#fff 65%)"></i></div><div class="tools">♥ ⇄ ⊕</div><h4>EARRINGS</h4><p class="price"><span class="now">$78.00</span></p><div class="stars">★★★★★</div></div>
  <div class="abs card" style="left:612px"><div class="pic"><i role="img" aria-label="Gold cuff bracelet" style="background:radial-gradient(#d9b24e,#fff 65%)"></i></div><div class="tools">♥ ⇄ ⊕</div><h4>BRACELETS</h4><p class="price"><span class="now">$56.00</span><s>$66.00</s></p><div class="stars">★★★★★</div></div>
  <div class="abs card" style="left:868px"><div class="pic"><i role="img" aria-label="Diamond ring set" style="background:radial-gradient(#cfcfcf,#fff 65%)"></i></div><div class="tools">♥ ⇄ ⊕</div><h4>RINGS</h4><p class="price"><span class="now">$48.00</span><s>$66.00</s></p><div class="stars">★★★★★</div></div>
</section>

<section class="section strip">
  <div class="tile" role="img" aria-label="Gold drop earrings on cream background" style="background:linear-gradient(90deg,#b8733a 0%,#e8b87c 40%,#f4d7a8 100%)">
    <div class="txt" style="left:210px;color:#3a2612"><h3 style="font-size:20px;line-height:24px;color:#3a2612">Women's<br>COLLECTION</h3><p class="sub" style="color:#a0642a">$133.4</p><span class="btn" style="border-color:#3a2612">SHOP NOW</span></div>
  </div>
  <div class="tile" role="img" aria-label="Woman wearing a gold bracelet" style="background:linear-gradient(90deg,#3a2a22,#7a5a44)">
    <div class="txt" style="left:40px"><h3>LATEST<br>New<br>Collections</h3><span class="btn dark">SHOP NOW</span></div>
  </div>
  <div class="tile" role="img" aria-label="Gold and gemstone necklace on dark cloth" style="background:linear-gradient(90deg,#2e1a1a,#5a3028 60%,#8a5a3a)">
    <div class="txt" style="left:30px"><h3>BEST<br>DEALS</h3><p class="sub">Accessorium</p><span class="btn dark">SHOP NOW</span></div>
  </div>
</section>

<section class="section testimonials">
  <div class="abs t-box"></div>
  <div class="abs quote">“</div>
  <h2 class="section-title">TESTIMONIALS</h2>
  <div class="abs t-col" style="left:150px">
    <p>The ring I ordered arrived beautifully wrapped and looked even lovelier in person. The team answered every question I had about the stone and helped me choose the perfect size for my mother's birthday.</p>
    <div class="person"><span class="avatar" role="img" aria-label="Customer portrait"></span><span><b>CHARLOTTE WINTERS</b><small>Customer</small></span></div>
  </div>
  <div class="abs t-col" style="left:630px">
    <p>Wonderful service from start to finish. My earrings came quickly and the care card explained how to keep them sparkling. I have already shared the store with my sisters and friends.</p>
    <div class="person"><span class="avatar" role="img" aria-label="Customer portrait"></span><span><b>HELENA MARSH</b><small>Customer</small></span></div>
  </div>
  <div class="abs dots"><i></i><i></i><i></i><i></i></div>
</section>

<section class="section blog">
  <h2 class="section-title">LATEST BLOG POSTS</h2>
  <div class="post-img" role="img" aria-label="Diamond necklace on black velvet" style="left:100px;top:220px;width:340px;height:268px;background:radial-gradient(circle at 50% 40%,#8a8a8a,#1a1a1a 70%)"></div>
  <div class="date" style="left:100px;top:432px">MAY<br>2017</div>
  <div class="post-txt" style="left:440px;top:220px;width:320px;height:268px"><h4>SED DO EIUSMOD TEMPOR INCIDIDUNT LOREM IPSUM MAGNA ALIQUA</h4><p>How to pick a diamond that suits your style, and the four simple checks every buyer should know before choosing.</p><a>Read more ›</a></div>
  <div class="post-img" role="img" aria-label="Gold jewellery with perfume bottles" style="left:760px;top:220px;width:340px;height:268px;background:linear-gradient(135deg,#6a4a2a,#c9a05a 60%,#3a2a1a)"></div>
  <div class="date" style="left:1044px;top:432px">MAY<br>2017</div>
  <div class="post-txt" style="left:100px;top:500px;width:320px;height:268px"><h4>UT ENIM AD MINIM VENIAM, QUIS NOSTRUD EXERCITATION</h4><p>Caring for pearls at home: gentle cleaning, safe storage and why they love to be worn often.</p><a>Read more ›</a></div>
  <div class="post-img" role="img" aria-label="Emerald ring with diamonds" style="left:420px;top:500px;width:340px;height:268px;background:radial-gradient(circle at 55% 55%,#1e7a4a,#e8e8e8 60%)"></div>
  <div class="date" style="left:420px;top:500px">MAY<br>2017</div>
  <div class="post-txt" style="left:760px;top:500px;width:340px;height:268px"><h4>EXCEPTEUR SINT OCCAECAT CUPIDATAT NON PROIDENT</h4><p>Family heirlooms and the stories they carry, from grandmother's brooch to a daughter's first ring.</p><a>Read more ›</a></div>
</section>

<section class="section perks">
  <div class="abs perk" style="left:100px"><svg width="34" height="34"><circle cx="17" cy="17" r="14" fill="none" stroke="#c9a26b" stroke-width="2"/><path d="M3 17h28M17 3c-6 8-6 20 0 28M17 3c6 8 6 20 0 28" fill="none" stroke="#c9a26b" stroke-width="1.5"/></svg><span><b>WORLDWIDE DELIVERY</b><small>On orders over $70.00</small></span></div>
  <div class="abs perk" style="left:360px"><svg width="34" height="34"><rect x="4" y="12" width="26" height="18" fill="none" stroke="#c9a26b" stroke-width="2"/><path d="M4 12h26M17 12v18M17 12c-4-8-10-4-6 0M17 12c4-8 10-4 6 0" fill="none" stroke="#c9a26b" stroke-width="1.5"/></svg><span><b>20% OFF YOUR FIRST ORDER</b><small>Sign up and save today</small></span></div>
  <div class="abs perk" style="left:620px"><svg width="34" height="34"><rect x="3" y="8" width="28" height="19" fill="none" stroke="#c9a26b" stroke-width="2"/><path d="M3 8l14 11 14-11" fill="none" stroke="#c9a26b" stroke-width="2"/></svg><span><b>INVITE FRIENDS &amp; GET OFF</b><small>Share and earn rewards</small></span></div>
  <div class="abs pay" style="left:906px"><i></i><i></i><i></i><i></i></div>
</section>

<footer class="section footer">
  <div class="abs contacts">
    <h4>CONTACTS</h4>
    <ul>
      <li><svg width="14" height="18"><path d="M7 1a6 6 0 016 6c0 5-6 10-6 10S1 12 1 7a6 6 0 016-6z" fill="none" stroke="#c9a26b" stroke-width="1.5"/><circle cx="7" cy="7" r="2" fill="#c9a26b"/></svg><span>18 Lantern Lane, Sheung Wan,<br>Hong Kong</span></li>
      <li><svg width="14" height="16"><path d="M3 1l3 3-2 3c1 2 3 4 5 5l3-2 3 3-2 2C8 15 0 7 1 3z" fill="#c9a26b"/></svg><span>Phone: (852) 3018 4420</span></li>
      <li><svg width="16" height="12"><rect x="1" y="1" width="14" height="10" fill="none" stroke="#c9a26b" stroke-width="1.5"/><path d="M1 1l7 6 7-6" fill="none" stroke="#c9a26b" stroke-width="1.5"/></svg><span>Email: hello@velistojewels.com</span></li>
    </ul>
    <div class="social"><i></i><i></i><i></i></div>
  </div>
  <div class="abs fcol" style="left:608px;top:60px"><h4>ABOUT US</h4><ul><li>Our Story</li><li>Wholesale</li></ul></div>
  <div class="abs fcol" style="left:800px;top:60px"><h4>SHOPPING</h4><ul><li>Orders</li><li>Returns</li><li>Size Guide</li></ul></div>
  <div class="abs fcol" style="left:980px;top:60px"><h4>CUSTOMER CARE</h4><ul><li>Delivery</li><li>FAQ</li><li>Care &amp; Warranty</li><li>Contact Us</li></ul></div>
  <div class="abs news"><h4>NEWSLETTER SIGN UP</h4><div class="field"><span></span><b>SUBSCRIBE</b></div></div>
</footer>
<div class="section bottom">© Copyright 2017 VELISTO JEWELLERY. All Rights Reserved</div>

</body>
</html>
```